Vetern Mailer for Mortgage Refinance

Hello, I need some options in my KB mailers we send out here in the USA! A sample of our mailer has been included. I need all the verbiage the same. The data merge points need to stay on too. Please make this pop. We have a high end PELDO printer and a Z auto folding machine. Letter goes into a number 10 envelope with windows. So lets see what you can do. One with colors below is our company colors and then one black, white, gray.
Blue - 3399FF------ R 51 G 153 B 255
Orange - FF9933----- R 255 G 153 B 51
Black – 333333------ R 51 G 51 B 51
White – FFFFFF------ R 255 G 255 B 255

Target Market(s)

United States Military Service Members

Industry/Entity Type

Mortgage Lender

Requirements
Must have
• Margins for folding with Z and Number 10 Envelope with two windows

```html
<!DOCTYPE html>
<html lang="en">
<head>
<meta charset="utf-8">
<title>KB Refinance Mailer</title>
<link rel="stylesheet" href="https://fonts.googleapis.com/css2?family=Poppins:wght@400;500;600;700&display=swap">
<style>
:root{
  --blue:#3399ff;
  --orange:#ff9933;
  --ink:#333333;
  --white:#ffffff;
  --bar:#e6e6e6;
  --backdrop:#c9c9c9;
  --house-warm:#d9c3a0;
}
*{box-sizing:border-box;margin:0;padding:0}
html,body{width:1200px;height:3114px;overflow:hidden}
body{background:var(--backdrop);font-family:"Poppins",sans-serif;color:var(--ink);position:relative}
.letter{position:absolute;left:100px;top:910px;width:1000px;height:1294px;background:var(--white);box-shadow:0 10px 30px rgba(0,0,0,.25)}
.abs{position:absolute}
.hyph{hyphens:auto;-webkit-hyphens:auto}
.field-bar{position:absolute;height:20px;background:var(--bar);font-size:15px;line-height:20px}
.field-bar .tag{display:inline-block;height:100%;background:var(--orange);color:var(--white);padding-left:10px}
.notice{left:50px;top:134px;width:350px;font-size:16px;line-height:20px}
.merge-address{left:50px;top:227px;font-size:16.5px;line-height:20px;letter-spacing:.5px}
.offer-box{left:637px;top:46px;width:309px;height:168px;border:2px solid #555}
.offer-box .month{position:absolute;left:9px;width:289px;height:28px;background:var(--bar);border:1px solid #777;text-align:center;font-size:17px;line-height:26px}
.offer-box .amount{position:absolute;left:0;right:0;top:98px;text-align:center;font-weight:700;font-size:56px;line-height:56px;color:var(--orange)}
.defer{left:637px;top:230px;width:309px;text-align:center;font-size:18px;line-height:20px}
sup{font-size:.55em;line-height:0}
.toll{left:637px;top:313px;width:309px;text-align:center}
.toll .label{font-weight:700;font-size:30px;line-height:34px;color:var(--blue)}
.toll .number{font-weight:600;font-size:27px;line-height:34px;display:flex;align-items:center;justify-content:center;gap:10px}
.toll .hours{font-size:18.5px;line-height:34px}
.letter-copy{left:54px;top:493px;width:390px}
.greeting{font-weight:600;font-size:19px;line-height:24px;margin-bottom:12px}
.body-copy{font-size:14.5px;line-height:17.8px}
.callout{margin-top:6px;width:340px;font-weight:700;font-size:21px;line-height:25px;color:var(--blue)}
.hero{left:458px;top:475px;width:535px;height:332px;background:radial-gradient(ellipse at 65% 45%,var(--house-warm) 0%,#efe6d8 45%,var(--white) 75%)}
.benefits{left:52px;top:882px;width:894px;height:161px;display:flex;border-radius:12px;overflow:hidden;color:var(--white)}
.benefits .col{flex:1;padding:12px 24px}
.benefits .extra{background:var(--orange)}
.benefits .program{background:var(--blue);padding-left:40px}
.benefits h3{font-weight:600;font-size:21px;line-height:28px;margin-bottom:2px}
.benefits li{list-style:none;font-size:15px;line-height:23px;display:flex;align-items:center;gap:7px;white-space:nowrap}
.tick{width:11px;height:11px;border-radius:50%;background:var(--white);flex:none;position:relative}
.tick::after{content:"";position:absolute;left:3.5px;top:2px;width:3px;height:5px;border:solid var(--orange);border-width:0 1.5px 1.5px 0;transform:rotate(45deg)}
.program .tick::after{border-color:var(--blue)}
.closing{left:50px;top:1064px;width:370px}
.urgency{font-size:14.5px;line-height:17.6px}
.cash{margin-top:20px;font-weight:600;font-size:26px;line-height:30px;white-space:nowrap}
.cash .figure{display:block;color:var(--blue);font-size:24px;line-height:30px}
.brand{left:514px;top:1058px;font-size:30px;font-weight:400;letter-spacing:3px;color:var(--blue)}
.company{left:512px;top:1178px;width:470px}
.company .name{font-weight:600;font-size:17px;line-height:22px}
.company .addr{font-size:15.5px;line-height:22px;display:flex;align-items:center;gap:5px;white-space:nowrap}
.license{display:flex;align-items:center;margin-top:4px}
.license .k{background:var(--blue);color:var(--white);font-weight:600;font-size:18px;width:87px;text-align:center;line-height:24px}
.license .v{background:var(--orange);color:var(--white);font-weight:600;font-size:18px;width:104px;text-align:center;line-height:24px;margin-left:2px}
.license .note{font-size:12px;margin-left:26px;white-space:nowrap}
</style>
</head>
<body>
<main class="letter">
  <div class="field-bar" style="left:50px;top:50px;width:343px"><span class="tag" style="width:156px">RE:</span></div>
  <div class="field-bar" style="left:50px;top:81px;width:343px"><span class="tag" style="width:156px">Loan ID Number</span></div>

  <p class="abs notice">Summit Crest Home Loans LLC Is not affiliated with your current lender nor is it an agency of the Federal Government.</p>
  <p class="abs merge-address">&lt;&lt;first_name&gt;&gt; &lt;&lt;last_name&gt;&gt;<br>&lt;&lt;address&gt;&gt;<br>&lt;&lt;city_state_zip&gt;&gt;</p>

  <div class="abs offer-box">
    <div class="month" style="top:11px">Close_month</div>
    <div class="month" style="top:46px">Skip_month</div>
    <div class="amount">$0</div>
  </div>
  <p class="abs defer">You may be able to defer<br>your next two payments.<sup>1</sup></p>

  <div class="abs toll">
    <div class="label">CALL TOLL FREE</div>
    <div class="number">
      <svg width="22" height="22" viewBox="0 0 22 22" aria-hidden="true"><circle cx="11" cy="11" r="9.5" fill="none" stroke="#ff9933" stroke-width="2.5"/><path d="M7 6.5c.8-.6 1.6-.4 2 .4l.8 1.6c.3.6.1 1.2-.4 1.5l-.6.4c.5 1.3 1.4 2.3 2.7 2.9l.4-.6c.4-.5 1-.6 1.5-.3l1.5.9c.7.4.9 1.3.3 2-1 1.1-2.6 1.2-4.6-.2-2.3-1.6-4-4.2-4-6.4 0-1 .2-1.8.4-2.2z" fill="#ff9933"/></svg>
      <span>555 0142 7788</span>
    </div>
    <div class="hours">Weekdays 6 a.m. to 5 p.m. PST</div>
  </div>

  <div class="abs letter-copy">
    <h2 class="greeting">Dear Dana ,</h2>
    <p class="body-copy hyph">We are contacting you regarding your &lt;&lt;balance&gt;&gt; KB loan. Our review has indicated that because of homes appreciating in &lt;&lt;city&gt;&gt;, you may now qualify for additional benefits. These benefits may include lowering your monthly mortgage payment, deferring up to two payments, refund of escrow, and $35,000 or more cash-out.<sup>3</sup> Call our KB Program Specialist at &lt;&lt;phone_number&gt;&gt; at your earliest convenience to receive a detailed explanation of how you may be able to access these benefits.<sup>4</sup></p>
    <p class="callout">You may also receive a check back from your escrow account.<sup>2</sup></p>
  </div>

  <div class="abs hero" role="img" aria-label="Photo of a small wooden toy house with a red roof beside stacks of gold coins and a house key"></div>

  <section class="abs benefits">
    <div class="col extra">
      <h3>Additional Benefits Include:</h3>
      <ul>
        <li><span class="tick"></span>100% LTV Cash-Out Available</li>
        <li><span class="tick"></span>Pay off High Interest Debt</li>
        <li><span class="tick"></span>Complete a long overdue home renovation</li>
        <li><span class="tick"></span>No out-of-pocket appraisal deposit</li>
        <li><span class="tick"></span>No Private Mortgage Insurance</li>
      </ul>
    </div>
    <div class="col program">
      <h3>KB IRRRL Benefits</h3>
      <ul>
        <li><span class="tick"></span>Reduce Your Current Interest Rate</li>
        <li><span class="tick"></span>Mortgage-Only Credit Report</li>
        <li><span class="tick"></span>No Appraisal Required</li>
        <li><span class="tick"></span>Fast Closings in 8-14 days</li>
        <li><span class="tick"></span>No Income or Asset Verification Required</li>
      </ul>
    </div>
  </section>

  <div class="abs closing">
    <p class="urgency hyph">We recommend you call our office at &lt;&lt;phone_number&gt;&gt; within the next 3-5 business days as market rates fluctuate. By taking action now your next mortgage payment may not be due until &lt;&lt;next_pay_month&gt;&gt;.2 To avoid further delay, please call today.</p>
    <p class="cash">CASH OUT OPTIONS (TAX FREE)<span class="figure">$35,000 OR MORE</span></p>
  </div>

  <div class="abs brand">SUMMIT CREST</div>
  <div class="field-bar" style="left:516px;top:1113px;width:433px;font-size:14px"><span class="tag" style="width:64px">Phone:</span></div>
  <div class="field-bar" style="left:516px;top:1140px;width:433px;font-size:14px"><span class="tag" style="width:134px">Loan ID Number:</span></div>

  <div class="abs company">
    <div class="name">Summit Crest Home Loans LLC</div>
    <div class="addr">
      <svg width="14" height="18" viewBox="0 0 14 18" aria-hidden="true"><path d="M7 0C3.1 0 0 3 0 6.8 0 11.5 7 18 7 18s7-6.5 7-11.2C14 3 10.9 0 7 0z" fill="#ff9933"/><circle cx="7" cy="6.8" r="2.6" fill="#fff"/></svg>
      <span>2280 Cedar Ridge Rd Ste 120 Mesa, AZ 85201</span>
    </div>
    <div class="license"><span class="k">NMLS</span><span class="v">1048862</span><span class="note">*Please see reverse for disclaimer</span></div>
  </div>
</main>
</body>
</html>
```